Harbor Ledger Funds Bus card and Logo

I need a logo design and Bus card design. The fund focuses on evaluating and investing in minerals (sub-surface rights) and real estate.

Harbor ledger refers to a book of knowledge that each plebe gets when entering the Kelmont Marine Academy (my alma mater)

Target Market(s)

Investors and financial advisors

Contact Information for Business Card

Simple - perhaps a logo with a theme on book of knowledge

Logo Text

Ex Scientia Imperium

Font styles to use
Serif
Sans Serif

Colors

Designer to choose colors to be used in the design.

Requirements
Must have
• memorable logo that is relatively simple

```html
<!DOCTYPE html>
<html lang="en">
<head>
<meta charset="utf-8">
<title>Harbor Ledger Funds – Business Card</title>
<link rel="stylesheet" href="https://fonts.googleapis.com/css2?family=Questrial&display=swap">
<style>
  :root {
    --page-bg: #e9e8e6;
    --card-bg: #ffffff;
    --brand-blue: #0a5a9c;
    --name-blue: #0c5596;
    --accent-purple: #6f6ab0;
    --on-blue: #ffffff;
  }
  html, body {
    margin: 0;
    width: 1200px;
    height: 902px;
    overflow: hidden;
    background: var(--page-bg);
  }
  .business-card {
    position: absolute;
    left: 80px;
    top: 155px;
    width: 1040px;
    height: 592px;
    background: var(--card-bg);
    border-radius: 22px;
    overflow: hidden;
    box-shadow: 0 6px 24px rgba(0,0,0,0.12);
    font-family: "Questrial", "Helvetica Neue", Arial, sans-serif;
  }
  .footer-band {
    position: absolute;
    inset: 0;
    width: 1040px;
    height: 592px;
  }
  .name-marker {
    position: absolute;
    left: 0;
    top: 100px;
    width: 10px;
    height: 58px;
    background: var(--accent-purple);
  }
  .contact-block {
    position: absolute;
    left: 53px;
    top: 98px;
    color: var(--name-blue);
  }
  .person-name {
    margin: 0;
    font-size: 33px;
    line-height: 36px;
    font-weight: 400;
    letter-spacing: 0.2px;
  }
  .person-title {
    margin: 0;
    font-size: 24px;
    line-height: 28px;
    color: var(--accent-purple);
  }
  .postal-address {
    margin: 34px 0 0;
    font-style: normal;
    font-size: 24px;
    line-height: 33px;
  }
  .contact-list {
    list-style: none;
    margin: 36px 0 0;
    padding: 0;
    font-size: 25px;
    line-height: 37px;
  }
  .contact-list li {
    display: flex;
    align-items: center;
    gap: 16px;
  }
  .contact-icon {
    width: 22px;
    height: 22px;
    flex: none;
  }
  .brand-name {
    position: absolute;
    left: 560px;
    top: 150px;
    width: 454px;
    margin: 0;
    text-align: center;
    font-size: 46px;
    line-height: 56px;
    font-weight: 400;
    color: var(--brand-blue);
  }
  .website {
    position: absolute;
    right: 60px;
    top: 515px;
    margin: 0;
    color: var(--on-blue);
    font-size: 24px;
    letter-spacing: 2px;
  }
</style>
</head>
<body>
  <main class="business-card">
    <svg class="footer-band" viewBox="0 0 1040 592" aria-hidden="true">
      <path fill="var(--accent-purple)" d="M0 462 Q520 430 1040 462 L1040 472 Q520 440 0 472 Z"/>
      <path fill="var(--brand-blue)" d="M0 482 Q520 450 1040 482 L1040 592 L0 592 Z"/>
    </svg>

    <span class="name-marker" aria-hidden="true"></span>

    <section class="contact-block">
      <h1 class="person-name">DANIEL BROOKS</h1>
      <p class="person-title">President</p>
      <address class="postal-address">PO BOX 123, your address<br>2nd street Fairhaven</address>
      <ul class="contact-list">
        <li>
          <svg class="contact-icon" viewBox="0 0 22 22" aria-hidden="true">
            <rect x="4" y="1.5" width="14" height="19" rx="2" fill="none" stroke="var(--name-blue)" stroke-width="2"/>
            <rect x="7" y="16" width="8" height="2" fill="var(--name-blue)"/>
          </svg>
          <span>555 555 5555</span>
        </li>
        <li>
          <svg class="contact-icon" viewBox="0 0 22 22" aria-hidden="true">
            <rect x="1" y="5" width="20" height="13" fill="var(--accent-purple)"/>
            <path d="M1 5 L11 13 L21 5" fill="none" stroke="#fff" stroke-width="1.6"/>
          </svg>
          <span>info@harborledgerfunds.com</span>
        </li>
      </ul>
    </section>

    <p class="brand-name">Harbor Ledger<br>Funds LLC</p>

    <p class="website">www.harborledgerfunds.com</p>
  </main>
</body>
</html>
```